Home page design for my business

My business will be selling templated drive-in movie theater websites. I would like my business to state to my customers that they get a free website (with hosting fees) where they can take ticket sales digitally. My company will be called Reel-Lanternworks (for Drive In Movie Theatres).

Here are some websites of my potential customers:
https://www.pelorcrest.example/
https://moonglowcinemas.example/
https://oakridgeoutdoorscreen.example/

```html
<!DOCTYPE html>
<html lang="en">
<head>
<meta charset="utf-8">
<title>Reel-Lanternworks — Free Websites for Drive-In Movie Theatres</title>
<link rel="stylesheet" href="https://fonts.googleapis.com/css2?family=Anton&family=Roboto+Condensed:wght@300;400;500;700&display=swap">
<style>
:root{
  --backdrop:#0d0d0d;
  --page:#ffffff;
  --ink:#111111;
  --body-grey:#6f6f6f;
  --amber:#b9681c;
  --dark-btn:#141414;
  --white:#ffffff;
}
*{margin:0;padding:0;box-sizing:border-box}
html,body{width:1200px;height:3200px;overflow:hidden}
body{
  background:linear-gradient(135deg,#151515 0%,#0a0a0a 50%,#161616 100%);
  font-family:"Roboto Condensed",Arial,sans-serif;
  color:var(--ink);
  position:relative;
}
.page{position:absolute;left:144px;top:60px;width:912px;height:3079px;background:var(--page);overflow:hidden}
.abs{position:absolute}

/* header */
.site-header{left:0;top:0;width:912px;height:114px}
.phone{right:50px;top:6px;display:flex;align-items:center;gap:6px;font-weight:700;font-size:20px;letter-spacing:.3px}
.brand{left:51px;top:34px;display:flex;align-items:center;gap:12px}
.brand-dot{width:40px;height:40px;border-radius:50%;background:var(--ink)}
.brand-name{font-family:"Anton",Impact,sans-serif;font-size:32px;color:var(--ink);letter-spacing:.2px}
.main-nav{right:50px;top:57px;display:flex;gap:31px;font-weight:700;font-size:14px;text-transform:uppercase}
.main-nav a{color:var(--ink);text-decoration:none;padding-bottom:5px}
.main-nav a.active{border-bottom:2px solid var(--ink)}

/* hero */
.hero{left:0;top:114px;width:912px;height:410px;
  background:linear-gradient(180deg,#7e86a8 0%,#5b6078 35%,#3a3d4a 65%,#24252c 100%)}
.hero-title{left:0;top:210px;width:912px;text-align:center;font-family:"Anton",Impact,sans-serif;font-size:76px;line-height:1;color:var(--white)}
.btn{display:flex;align-items:center;justify-content:center;border-radius:32px;color:var(--white);font-weight:700;font-size:17px;text-transform:uppercase;text-decoration:none;height:63px}
.btn-amber{background:var(--amber)}
.btn-dark{background:var(--dark-btn)}
.hero .btn{position:absolute;left:368px;top:329px;width:178px}
.hero-dots{right:40px;top:364px;display:flex;gap:5px}
.hero-dots span{width:8px;height:8px;border-radius:50%;background:var(--white)}
.hero-dots span.on{background:var(--amber)}

/* welcome */
.section-title{font-family:"Anton",Impact,sans-serif;color:var(--ink);text-align:center;line-height:1;width:912px;left:0}
.welcome-title{top:625px;font-size:78px}
.welcome-text{left:51px;top:732px;width:810px;text-align:center;font-weight:300;font-size:17px;line-height:32px;color:var(--body-grey)}
.welcome-actions{left:272px;top:937px;display:flex;gap:10px}
.welcome-actions .btn{width:179px}

/* gallery */
.gallery{left:8px;top:1068px;display:flex;gap:8px}
.gallery .shot{width:293px;height:259px}
.shot-1{background:linear-gradient(160deg,#1f3f9a 0%,#2d56c0 45%,#caa88a 75%,#3a2a22 100%)}
.shot-2{background:linear-gradient(180deg,#6f8fc8 0%,#e79a5b 35%,#f0a53a 48%,#4c5b3a 70%,#3b4530 100%)}
.shot-3{background:linear-gradient(180deg,#8aa4c6 0%,#b9c8da 40%,#5f7d4a 70%,#3f5a32 100%)}

/* tickets */
.tickets-title{top:1430px;font-size:78px}
.ticket-card{top:1555px;width:442px}
.ticket-card .shot{width:442px;height:381px}
.card-1{left:8px}
.card-2{left:461px}
.card-1 .shot{background:linear-gradient(170deg,#1d1b1e 0%,#2a2a34 40%,#3c4150 60%,#161618 100%)}
.card-2 .shot{background:linear-gradient(180deg,#0d1a2c 0%,#1d3b5c 45%,#2d5573 60%,#0b1624 100%)}
.ticket-text{margin-top:40px;text-align:center;font-weight:500;font-size:19px;line-height:29px;color:#222}
.ticket-card .btn{width:179px;margin:27px auto 0}

/* video band */
.video-band{left:0;top:2210px;width:912px;height:490px;
  background:radial-gradient(ellipse at 50% 30%,#6d6d6d 0%,#3a3a3a 30%,#1a1a1a 60%,#0c0c0c 100%)}
.play{left:417px;top:205px}
.video-text{left:0;top:318px;width:912px;text-align:center;font-weight:700;font-size:35px;line-height:41px;color:var(--white)}

/* footer */
.site-footer{left:0;top:2700px;width:912px;height:379px}
.footer-brand{left:0;width:912px;top:60px;display:flex;justify-content:center;align-items:center;gap:16px}
.footer-brand .brand-dot{width:56px;height:56px}
.footer-brand .brand-name{font-size:44px}
.footer-nav{left:0;width:912px;top:176px;display:flex;justify-content:center;gap:28px;font-weight:700;font-size:21px;text-transform:uppercase}
.footer-nav a{color:var(--ink);text-decoration:none}
.footer-nav .sep{font-weight:400}
.copyright{left:0;width:912px;top:237px;text-align:center;font-size:14px;color:#222}
.social{left:0;width:912px;top:293px;display:flex;justify-content:center;gap:8px}
.social span{width:32px;height:32px;border-radius:50%;background:var(--ink)}
</style>
</head>
<body>
<div class="page">

  <header class="site-header abs">
    <div class="phone abs">
      <svg width="36" height="36" viewBox="0 0 36 36" aria-hidden="true">
        <circle cx="18" cy="18" r="16" fill="none" stroke="#111" stroke-width="2.5"/>
        <path d="M12 10c1-1 2.5-1 3 0l2 3.5c.5 1 0 2-1 2.5l-1 .6c.8 2 2.4 3.6 4.4 4.4l.6-1c.5-1 1.5-1.5 2.5-1l3.5 2c1 .5 1 2 0 3l-1.5 1.5c-5 1-13-7-12-12z" fill="#111"/>
      </svg>
      <span>+1 555 014 2290</span>
    </div>
    <div class="brand abs">
      <span class="brand-dot"></span>
      <span class="brand-name">Reel-Lanternworks</span>
    </div>
    <nav class="main-nav abs">
      <a class="active" href="#">Home</a>
      <a href="#">About</a>
      <a href="#">Online Tickets</a>
      <a href="#">FAQ</a>
      <a href="#">Contact</a>
    </nav>
  </header>

  <section class="hero abs" role="img" aria-label="Dusk photo of a drive-in lot with parked cars facing a large outdoor screen">
    <h1 class="hero-title abs">Reel-Lanternworks</h1>
    <a class="btn btn-amber" href="#">Get Started</a>
    <div class="hero-dots abs"><span></span><span class="on"></span><span></span><span></span></div>
  </section>

  <h2 class="section-title welcome-title abs">Welcome</h2>
  <p class="welcome-text abs">Reel-Lanternworks builds websites made only for drive-in movie theatres. Every theatre that joins us gets a free, ready-to-launch website from our proven templates, with hosting fees included, so there is nothing to pay up front and no server to manage. Your site comes with digital ticket sales built in: guests pick a showtime, choose their car pass and pay online before they arrive, while you track sales from one simple dashboard. Update your showtimes, concession specials and gate rules in minutes, and let your screen shine online as bright as it does at night under the stars.</p>
  <div class="welcome-actions abs">
    <a class="btn btn-amber" href="#">Read More</a>
    <a class="btn btn-dark" href="#">Online Tickets</a>
  </div>

  <div class="gallery abs">
    <div class="shot shot-1" role="img" aria-label="Vintage drive-in theatre screen tower against a deep blue evening sky"></div>
    <div class="shot shot-2" role="img" aria-label="Aerial view of a drive-in field full of cars at sunset"></div>
    <div class="shot shot-3" role="img" aria-label="Blank outdoor movie screen on a grassy field with a car in front"></div>
  </div>

  <h2 class="section-title tickets-title abs">Online Tickets</h2>
  <article class="ticket-card card-1 abs">
    <div class="shot" role="img" aria-label="Cars parked at night in front of a glowing drive-in screen"></div>
    <p class="ticket-text">Sell car passes online for every showtime,<br>with instant e-tickets your guests can scan<br>at the gate straight from their phones.</p>
    <a class="btn btn-amber" href="#">Book Tickets</a>
  </article>
  <article class="ticket-card card-2 abs">
    <div class="shot" role="img" aria-label="Friends watching a movie from inside a car at night"></div>
    <p class="ticket-text">Your free site and hosting are included,<br>so moviegoers can book, pay and plan<br>their night out before they ever arrive.</p>
    <a class="btn btn-amber" href="#">Book Tickets</a>
  </article>

  <section class="video-band abs" role="img" aria-label="Night scene of a mobile outdoor screen on a truck with car lights in the foreground">
    <svg class="play abs" width="78" height="78" viewBox="0 0 78 78" aria-hidden="true">
      <circle cx="39" cy="39" r="35" fill="#fff"/>
      <circle cx="39" cy="39" r="28" fill="#b9681c"/>
      <path d="M31 24l25 15-25 15z" fill="#fff"/>
    </svg>
    <p class="video-text abs">A free website for your drive-in theatre.<br>Hosting included, tickets sold online.</p>
  </section>

  <footer class="site-footer abs">
    <div class="footer-brand abs">
      <span class="brand-dot"></span>
      <span class="brand-name">Reel-Lanternworks</span>
    </div>
    <nav class="footer-nav abs">
      <a href="#">Home</a><span class="sep">/</span>
      <a href="#">About</a><span class="sep">/</span>
      <a href="#">Online Tickets</a><span class="sep">/</span>
      <a href="#">FAQ</a><span class="sep">/</span>
      <a href="#">Contact</a>
    </nav>
    <p class="copyright abs">Copyright © 2022 Reel-Lanternworks - All Rights Reserved &nbsp;|&nbsp; Privacy &nbsp;|&nbsp; Terms and Use</p>
    <div class="social abs" aria-label="Social links"><span></span><span></span><span></span></div>
  </footer>

</div>
</body>
</html>
```